BRELMONT SKY RALLY JULY 2017

INVITATION TO MEDICAL LECTURE AT BRELMONT SKYRALLY 2017, JULY 25TH, THIS WILL BE MAILED TO APPROX 750 AVIATION MEDICAL EXAMINERS, MDS.

Target Market(s)

Aviation Medical Examiners

Industry/Entity Type

Medical

Colors
ec1f27
3377b5

Requirements
Must have
• Front of postcard: Art to include Airplane, Medical / Staff of Medicine Icon,
• Back of postcard:
• GO BEYOND STANDARD LIPID TESTING AND IMPROVE CARDIAC RISK:
• BRELMONT SKY RALLY 2017, TUESDAY JULY 25th, CALDRO THEATRE
• 8:00-9:00 am “CODE BLUE AT 40,000 FEET” DR. MARTIN WELSBY
• 9:00-10:00 am “VERY HIGH RISK GROUPS WITH CORONARY HEART DISEASE, A NATIONAL EMERGENCY” DR. DANIEL FORWITH
• 10:00-11:00 am “BEYOND CHOLESTEROL, THE NEED FOR ADVANCED LIPIDS, APPLICATION TO PILOTS” DR. DANIEL FORWITH
• 11:00-12:00 am “PROTECTING THE COCKPIT, PILOTS AND UNDETECTED HEART DISEASE” DR. HOWARD BRISCOE
• 1:00-2:00 am “PERSONAL LIFESTYLE MODIFICATIONS TO DECREASE HEART DISEASE” JUNE TARVIN, NP
• RSVP: Melinda Fairchild 604-582-917
Nice to have
• ON BACK all info above to list medical presentations, Cardiac Heart Icon, (heart with rhythm logo), on left, address to attendee on the right
• ON FRONT: Color POP with AVIATION THEME
Should not have
• Fancy Font, (please keep it clean and simple, easy to read)

```html
<!DOCTYPE html>
<html lang="en">
<head>
<meta charset="utf-8">
<title>Brelmont Sky Rally – Medical Lecture Postcard</title>
<link href="https://fonts.googleapis.com/css2?family=Open+Sans:wght@600;700;800&family=Roboto+Condensed:wght@700&display=swap" rel="stylesheet">
<style>
  :root {
    --red: #ec1f27;
    --blue: #1e6fc4;
    --blue-bright: #1a8fe0;
    --blue-deep: #1560bd;
    --ink: #333333;
    --panel: #f0f0f0;
    --white: #ffffff;
    --line: #c8c8c8;
    --stage: #2b2b2b;
  }
  * { box-sizing: border-box; margin: 0; padding: 0; }
  html, body { width: 864px; height: 1200px; overflow: hidden; }
  body {
    background: var(--stage);
    font-family: "Open Sans", Arial, sans-serif;
    position: relative;
  }
  .postcard {
    position: absolute;
    left: 43px;
    width: 778px;
    height: 528px;
    overflow: hidden;
    background: var(--white);
  }
  .postcard--front { top: 51px; }
  .postcard--back { top: 619px; }

  .front-photo {
    position: absolute; inset: 0;
    background: linear-gradient(135deg, #e6eef4 0%, #cfdde8 45%, #b7cad9 100%);
  }
  .shape-layer { position: absolute; inset: 0; width: 778px; height: 528px; }

  .back-header {
    position: absolute;
    left: 0; top: 22px;
    width: 425px; height: 63px;
    background: var(--blue);
    color: var(--white);
    font-weight: 700;
    font-size: 16.5px;
    line-height: 23px;
    padding: 10px 0 0 36px;
  }
  .session-list {
    position: absolute;
    left: 36px; top: 106px;
    width: 360px;
    list-style: none;
  }
  .session {
    position: relative;
    padding-left: 19px;
    font-weight: 700;
    font-size: 13.8px;
    line-height: 20.3px;
    color: var(--ink);
    margin-bottom: 12px;
  }
  .session--last { white-space: nowrap; }
  .session::before {
    content: "";
    position: absolute;
    left: 1px; top: 4px;
    width: 5px; height: 10px;
    border-right: 2px solid var(--blue);
    border-bottom: 2px solid var(--blue);
    transform: rotate(40deg);
  }
  .highlight { color: var(--red); }

  .heart-icon { position: absolute; left: 496px; top: 12px; width: 112px; height: 86px; }
  .stamp-box {
    position: absolute;
    left: 640px; top: 46px;
    width: 94px; height: 93px;
    border: 1px solid var(--line);
  }
  .address-line {
    position: absolute;
    left: 504px; width: 230px;
    border-top: 1px solid var(--line);
  }

  .rsvp-bar {
    position: absolute;
    left: 0; top: 434px;
    width: 778px; height: 56px;
  }
  .rsvp-label {
    position: absolute;
    left: 372px; top: 13px;
    color: var(--white);
    font-weight: 800;
    font-size: 24px;
    line-height: 30px;
  }
  .rsvp-name {
    position: absolute;
    left: 474px; top: 9px;
    color: var(--white);
    font-weight: 600;
    font-size: 14.5px;
    line-height: 19px;
  }
  .rsvp-phone {
    position: absolute;
    left: 587px; top: 6px;
    color: var(--white);
    font-family: "Roboto Condensed", "Arial Narrow", sans-serif;
    font-weight: 700;
    font-size: 34px;
    line-height: 42px;
  }
</style>
</head>
<body>

<section class="postcard postcard--front">
  <div class="front-photo" role="img" aria-label="Photo of a doctor in a white coat with a stethoscope showing a tablet to an airline captain in uniform, in a bright airport terminal"></div>
  <svg class="shape-layer" viewBox="0 0 778 528" aria-hidden="true">
    <path d="M0 0 H200 C110 70 35 170 0 300 Z" fill="var(--blue)"/>
    <path d="M200 0 H232 C135 80 40 200 0 345 V300 C35 170 110 70 200 0 Z" fill="var(--white)"/>
    <path d="M232 0 H258 C150 90 45 225 0 372 V345 C40 200 135 80 232 0 Z" fill="var(--red)"/>
    <path d="M778 266 V298 C730 400 680 475 612 528 H586 C660 470 720 390 778 266 Z" fill="var(--blue)"/>
    <path d="M778 298 V330 C735 420 690 480 629 528 H612 C680 475 730 400 778 298 Z" fill="var(--white)"/>
    <path d="M778 330 V528 H629 C690 480 735 420 778 330 Z" fill="var(--red)"/>
  </svg>
</section>

<section class="postcard postcard--back">
  <svg class="shape-layer" viewBox="0 0 778 528" aria-hidden="true">
    <path d="M0 0 H398 C488 95 505 330 285 528 H0 Z" fill="var(--panel)"/>
    <path d="M398 0 H428 C528 110 520 360 315 528 H285 C505 330 488 95 398 0 Z" fill="var(--red)"/>
    <path d="M346 434 H452 L466 462 L452 490 H336 Z" fill="var(--red)"/>
    <path d="M452 434 H587 L601 462 L587 490 H452 L466 462 Z" fill="var(--blue-bright)"/>
    <path d="M587 434 H778 V490 H587 L601 462 Z" fill="var(--blue-deep)"/>
  </svg>

  <h1 class="back-header">GO BEYOND STANDARD LIPID TESTING<br>AND IMPROVE CARDIAC RISK:</h1>

  <ul class="session-list">
    <li class="session">BRELMONT SKY RALLY 2017,<br><span class="highlight">TUESDAY JULY 25th</span>, CALDRO THEATRE</li>
    <li class="session">8:00-9:00 am “<span class="highlight">CODE BLUE</span> AT 40,000 FEET”<br>DR. MARTIN WELSBY</li>
    <li class="session">9:00-10:00 am <span class="highlight">“VERY HIGH RISK GROUPS WITH CORONARY HEART DISEASE, A NATIONAL EMERGENCY”</span> DR. DANIEL FORWITH</li>
    <li class="session">10:00-11:00 am <span class="highlight">“BEYOND CHOLESTEROL,<br>THE NEED FOR ADVANCED LIPIDS, APPLICATION TO PILOTS”</span> DR. DANIEL FORWITH</li>
    <li class="session">11:00-12:00 am <span class="highlight">“PROTECTING THE COCKPIT, PILOTS AND UNDETECTED HEART DISEASE”</span><br>DR. HOWARD BRISCOE</li>
    <li class="session session--last">1:00-2:00 am <span class="highlight">“PERSONAL LIFESTYLE<br>MODIFICATIONS TO DECREASE HEART<br>DISEASE”</span> JUNE TARVIN, NP</li>
  </ul>

  <svg class="heart-icon" viewBox="0 0 112 86" role="img" aria-label="Heart with heartbeat line">
    <path d="M56 84 C30 64 10 48 10 27 C10 12 21 3 34 3 C44 3 52 9 56 17 C60 9 68 3 78 3 C91 3 102 12 102 27 C102 48 82 64 56 84 Z" fill="var(--red)"/>
    <polyline points="0,44 36,44 42,36 48,44 52,44 58,22 64,66 70,44 112,44" fill="none" stroke="var(--white)" stroke-width="2.5" stroke-linejoin="round"/>
  </svg>

  <div class="stamp-box"></div>
  <div class="address-line" style="top:259px"></div>
  <div class="address-line" style="top:306px"></div>
  <div class="address-line" style="top:352px"></div>

  <div class="rsvp-bar">
    <span class="rsvp-label">RSVP:</span>
    <span class="rsvp-name">MELINDA<br>FAIRCHILD</span>
    <span class="rsvp-phone">604-582-917</span>
  </div>
</section>

</body>
</html>
```